Web Design job: SaaS start-up needs a cutting-edge web design

What's Needed:
- All designs files created
- Fully coded implementation in HTML/CSS/Bootstrap
- Pages: 5 -- see content here http://www.TeamVerdexa.com
-- Home Page
-- The Hidden Value
-- Benefits
-- About us
-- Careers
- The existing site has the textual content for each page. We can tweak to meet specific designs if needed.
- You will need to update/create image and interactive content for pages.

Reference:
Our existing website has a lot of content on it for reference -
http://www.TeamVerdexa.com

Description:
We need a web design that focuses in the UX and conveys the idea of magically fixing company problems by way of using our software.

Home Page
The main goal is to Drive Sales of the SaaS tool. When a visitor lands on our home page they should see: What we do, How we can help their problem and How to contact us.
1. Quickly understand What We Do
-- we sell SaaS software.
-- Need to quickly convey what our software does. It's seems complicated but really its not. See the description in about us for more info and visit our existing site.

2. How we can help their problem
-- We aim to solve any problem related to employees
-- Even if the visitor does not have a specific problem in mind, there are several areas organizations can always improve: (some examples below)
---- Create Stronger, More Productive Teams
---- Build Better Communications Pathways
---- Encourage Innovation and Positive Change
---- Develop and Retain Strong "Company Culture"

3. Be able to Contact Us to get started
-- contacting us to get a sales lead is the ultimate goal.
-- the user should not have to hunt to contact us. needs to be easy.

Other Pages (Hidden Value, Benefit, About Us, Careers):
-- These are informative pages about our software and process.
-- If we grab the attention of the user on the home page then these are the pages that they will explore for more info.
-- Should be able to link to these pages from the main nav or from sections with the homepage. For example: What We Do sections could link to the benefits page. How we help their problem sections could link to the Hidden Value page. Regardless of what links to where, the idea is that we will be able to nav to other areas.

About Us:
Our company name is TeamVerdexa (as in Organizational Analysis). We provide a software as a service (SaaS) that uses a simple 6-question survey to analyze the relationships of people within an Organization and provide leaders with ground-breaking Insights about their teams, interactive social network data visualizations to explore their team's composition and we give detailed profiles of the key players (i.e, who are the Social Bridges, Who are the Knowledge Bottlenecks, Who are the Best Mentors, Who are the people that are completely disconnected/out of the loop). Leaders then use this information to make high level organizational decisions.

What's unique about our software:
-- Powerful analysis results from just a 6-question "pulse-surveys"
-- Innovative Tools for visually exploring the organization through relationships as opposed to org-chart
-- Get real-time results as opposed to waiting months with traditional methods
-- Traditional Org-charts represent the organization's skeleton, whereas we uncover the organization's neural network (how it solves problems).

Preferred fonts (but could be convinced otherwise if looks great):
-- Section titles - Aleo
-- Main body - Lato
-- TeamVerdexa logo - Philosopher

Things we like:
-- We like a big slider as the top of the landing page.

Colors to include:
-- Colors in the logo (red, blue, green, teal) as accent colors

Feel of the site:
-- Cutting-edge Software
-- Professional
-- Social Network flare (we analyze relationships)

Note:
If we find a great match with a designer there is strong possibility to continue the relationship with follow on work redesigning our web-based application.

Target Market(s)

Current customers are Morrow Pike & Fenwell, Clearbrook Valley Bank.
We target anyone that manages a large team. Such as Corporate Leaders, High Level Managers, HR Leaders

Industry/Entity Type

Business Software

Contact Information for Business Card

Logo image
Name of company "TEAMVERDEXA" In Philosopher font.
Tagline: "Unlock the Hidden Value In Your Teams"
Person's Name, Title, email, phone.

Coding

Coded - Design and coding required

Number of Pages Required

4 page

Font styles to use
Other font styles liked:
• Lato, Philosopher, Aero

Colors
ec1f27
0255a3

Requirements
Must have
• See description.
Nice to have
• Things we like:
• We like a big slider as the top of the landing page. Ours is a little clunky and outdated but something fresh and sleek would be great.
• Colors to include:
• We would like to use the colors in the logo as accent colors in the site to give a consistent look and feel.
• Feel of the site:
• Cutting-edge Software
• Professional
• Social Network flare (we analyze relationships)

```html
<!DOCTYPE html>
<html lang="en">
<head>
<meta charset="utf-8">
<title>Careers | TeamVerdexa</title>
<link rel="stylesheet" href="https://fonts.googleapis.com/css2?family=Aleo:wght@300;400;700&family=Lato:wght@400;700&display=swap">
<style>
:root{
  --brand-blue:#0255a3;
  --accent-teal:#6cc6e6;
  --accent-red:#ec1f27;
  --text:#4a4a4a;
  --heading:#2b2b2b;
  --panel:#f0f0f0;
  --rule:#d6d6d6;
  --white:#ffffff;
}
*{box-sizing:border-box;margin:0;padding:0}
html,body{width:1200px;height:1136px;overflow:hidden;background:var(--white)}
body{font-family:"Lato",sans-serif;color:var(--text);position:relative}
.hero{position:absolute;left:0;top:0;width:1200px;height:204px;
  background:linear-gradient(90deg,#6f7880 0%,#8b9198 35%,#9a9ea3 55%,#7e858c 80%,#6a7279 100%)}
.hero-photo{position:absolute;inset:0;background:radial-gradient(ellipse at 50% 120%,rgba(196,160,130,.35),transparent 60%)}
.brand{position:absolute;left:89px;top:36px;display:flex;align-items:center;gap:10px}
.brand-mark{width:26px;height:26px;border-radius:50%;background:var(--accent-red)}
.brand-name{font-family:"Lato",sans-serif;font-weight:700;font-size:21px;line-height:1;color:var(--white)}
.main-nav a{position:absolute;top:44px;color:var(--white);font-size:14px;text-decoration:none}
.main-nav a.current{color:var(--accent-teal)}
.main-nav a.current::before{content:"";position:absolute;left:0;right:0;top:-16px;height:2px;background:var(--accent-teal)}
.client-login{position:absolute;left:998px;top:32px;width:113px;height:40px;border:2px solid var(--white);
  color:var(--white);font-size:14px;display:flex;align-items:center;justify-content:center;text-decoration:none}
.page-title{position:absolute;top:108px;width:100%;text-align:center;color:var(--white);
  font-family:"Aleo",serif;font-weight:300;font-size:37px}
.job-tabs{position:absolute;left:0;top:204px;width:1200px;height:49px;background:var(--white);box-shadow:0 2px 4px rgba(0,0,0,.06)}
.job-tabs a{position:absolute;top:17px;font-size:12.5px;color:#222;text-decoration:none;white-space:nowrap}
.job-tabs a.active{color:#777}
.job-tabs a.active::before{content:"";position:absolute;left:0;right:0;top:-17px;height:2px;background:var(--accent-teal)}
.section{position:absolute;left:202px;width:796px}
.section-rule{width:40px;height:1px;background:var(--rule);margin-bottom:12px}
.section h2{font-family:"Aleo",serif;font-weight:300;font-size:28px;color:var(--heading);margin-bottom:6px}
p{font-size:13.2px;line-height:22.2px;letter-spacing:-0.15px;hyphens:auto;-webkit-hyphens:auto}
.comp-box{position:absolute;left:202px;top:483px;width:796px;height:204px;background:var(--panel);padding:42px 36px 0 40px}
.comp-box h3{font-family:"Aleo",serif;font-weight:700;font-size:18px;color:var(--heading);margin-bottom:12px}
.comp-box p{font-size:12.9px}
.divider{position:absolute;left:0;top:901px;width:1200px;height:1px;background:#ececec}
.apply-buttons{position:absolute;left:202px;top:1008px;display:flex;gap:6px}
.apply-buttons a{width:395px;height:39px;display:flex;align-items:center;justify-content:center;font-size:14px;text-decoration:none}
.btn-primary{background:var(--brand-blue);color:var(--white)}
.btn-outline{border:2px solid #ddd;color:#333}
.site-footer{position:absolute;left:0;top:1092px;width:1200px;height:44px;background:var(--brand-blue);color:var(--white);font-size:13.5px}
.site-footer span,.site-footer a{position:absolute;top:14px;color:var(--white);text-decoration:none}
</style>
</head>
<body>
<header class="hero">
  <div class="hero-photo" role="img" aria-label="Photo of a smiling team collaborating around a table"></div>
  <div class="brand">
    <div class="brand-mark"></div>
    <div class="brand-name">TeamVerdexa</div>
  </div>
  <nav class="main-nav">
    <a href="#" style="left:522px">Home</a>
    <a href="#" style="left:594px">The Hidden Value</a>
    <a href="#" style="left:738px">Benefits</a>
    <a href="#" style="left:823px">About us</a>
    <a href="#" class="current" style="left:915px">Careers</a>
  </nav>
  <a href="#" class="client-login">Client Login</a>
  <h1 class="page-title">Careers</h1>
</header>

<nav class="job-tabs">
  <a href="#" class="active" style="left:89px">Sales, System Integration Channel</a>
  <a href="#" style="left:308px">Sales, HR Business Intelligence</a>
  <a href="#" style="left:510px">Sales, System Integration Channel</a>
  <a href="#" style="left:730px">UI/UX Designer Intern</a>
  <a href="#" style="left:888px">Social Network Algorithms Intern</a>
</nav>

<section class="section" style="top:302px">
  <div class="section-rule"></div>
  <h2>About the Position</h2>
  <p>TeamVerdexa is looking for a key addition to round out our strong start-up team. This person should understand the challenges of new software and process implementation and adoption. Our platform enables the identification and leverage of key personnel for faster, more effective teams and successful implementations. A preference will be given for candidates with contacts facing this clear business challenge on a daily basis.</p>
</section>

<div class="comp-box">
  <h3>COMPENSATION</h3>
  <p>We are offering an early stage opportunity to demonstrate the ability to identify prospects, pitch the basic value props and participate in closing customers. An extensive sales background is not essential, but the ability to clearly speak with customers and articulate concise value points is necessary. Initially, compensation will be a generous percentage of revenue generated from targeted customers. Equity will be available for the right person working into our team and demonstrating strong value.</p>
</div>

<section class="section" style="top:728px">
  <div class="section-rule"></div>
  <h2>About Us</h2>
  <p>TeamVerdexa is the first company to offer a software platform for deep Social Capital analyses and employee profile development, with real-time exploratory capabilities. Our proprietary algorithms help companies optimize the organizational social “topology”, illustrating and improving the ways employees communicate and work together. We have conducted engagements with Global Top-Tier companies and have received stellar feedback.</p>
</section>

<div class="divider"></div>

<section class="section" style="top:944px">
  <div class="section-rule"></div>
  <h2>Apply online via</h2>
</section>
<div class="apply-buttons">
  <a href="#" class="btn-primary">JobHarbor</a>
  <a href="#" class="btn-outline">StartRoster</a>
</div>

<footer class="site-footer">
  <span style="left:89px">© 2016 TeamVerdexa. All Rights Reserved.</span>
  <a href="#" style="left:870px">Home</a>
  <a href="#" style="left:935px">The Hidden Value</a>
  <a href="#" style="left:1063px">About Us</a>
</footer>
</body>
</html>
```